Business Card Design for Property Development Company Director

I am looking for a professional and unforgettable business card design for our Director of our Property Development Company.
Please see attached .pptx file to find out what information to include. You don't have to follow the exact format shown in the file - I am interested to see your creative flair using the information provided.

```html
<!DOCTYPE html>
<html lang="en">
<head>
<meta charset="utf-8">
<title>Norvale Property Group – Business Card</title>
<link href="https://fonts.googleapis.com/css2?family=Montserrat:wght@400;500;600;700&display=swap" rel="stylesheet">
<style>
  :root {
    --bg: #efefef;
    --card: #ffffff;
    --brand-blue: #1f5bb5;
    --ink-grey: #4a4a4a;
    --muted-grey: #6b6b6b;
  }
  * { box-sizing: border-box; margin: 0; padding: 0; }
  html, body { width: 1200px; height: 800px; overflow: hidden; }
  body {
    background: var(--bg);
    font-family: "Montserrat", sans-serif;
    display: flex;
    align-items: center;
    justify-content: center;
    gap: 50px;
  }
  .card {
    width: 520px;
    height: 318px;
    background: var(--card);
    box-shadow: 0 2px 10px rgba(0,0,0,0.08);
    position: relative;
  }
  .brand {
    display: flex;
    align-items: center;
    gap: 10px;
  }
  .brand-square {
    width: 22px; height: 22px;
    background: var(--brand-blue);
  }
  .brand-name {
    color: var(--brand-blue);
    font-weight: 700;
    font-size: 21px;
    letter-spacing: 0.02em;
    text-transform: uppercase;
  }

  /* Front */
  .card-front .brand { position: absolute; left: 34px; top: 34px; }
  .licence {
    position: absolute; left: 34px; top: 72px;
    font-size: 12px; color: var(--ink-grey);
  }
  .licence strong { color: var(--brand-blue); font-weight: 600; }
  .person { position: absolute; left: 230px; top: 150px; }
  .person-name {
    color: var(--brand-blue);
    font-weight: 600;
    font-size: 21px;
    text-transform: uppercase;
    letter-spacing: 0.01em;
  }
  .person-role { font-size: 12.5px; color: var(--ink-grey); margin-bottom: 12px; }
  .address, .contact-line { font-size: 12.5px; color: var(--ink-grey); line-height: 1.5; }
  .contacts { margin-top: 4px; }
  .contact-line { display: flex; align-items: center; gap: 7px; }
  .contact-line svg { width: 10px; height: 10px; fill: var(--brand-blue); flex: none; }

  /* Back */
  .specialism {
    position: absolute; right: 40px; top: 36px;
    text-align: right;
    font-size: 13px; color: var(--muted-grey); line-height: 1.45;
  }
  .card-back .brand { position: absolute; left: 120px; top: 140px; }
  .card-back .brand-name { font-size: 26px; }
  .card-back .brand-square { width: 28px; height: 28px; }
  .invite {
    position: absolute; left: 40px; right: 40px; bottom: 38px;
    font-size: 12.5px; font-weight: 500; color: var(--ink-grey);
  }
  .invite .highlight { color: var(--brand-blue); text-transform: uppercase; }
</style>
</head>
<body>

  <section class="card card-front" aria-label="Business card front">
    <div class="brand">
      <span class="brand-square"></span>
      <span class="brand-name">Norvale Property Group</span>
    </div>
    <p class="licence"><strong>Real Estate Lic.</strong> 1002345 &amp; 1002346</p>

    <div class="person">
      <h1 class="person-name">Daniel Marsh</h1>
      <p class="person-role">Director</p>
      <p class="address">42 Harlow St<br>Fitzroy VIC 3065, Australia</p>
      <div class="contacts">
        <p class="contact-line">
          <svg viewBox="0 0 10 10" aria-hidden="true"><path d="M2 0.5 L3.6 2.6 L2.7 3.6 C3.3 5 4.8 6.6 6.3 7.3 L7.4 6.4 L9.5 8 L8.4 9.5 C4.5 9.2 0.8 5.5 0.5 1.6 Z"/></svg>
          0412 600 318
        </p>
        <p class="contact-line">
          <svg viewBox="0 0 10 10" aria-hidden="true"><path d="M0.5 2 H9.5 V8.5 H0.5 Z M1.3 2.6 L5 5.4 L8.7 2.6 Z" fill-rule="evenodd"/></svg>
          daniel@norvale.com.au
        </p>
        <p class="contact-line">
          <svg viewBox="0 0 10 10" aria-hidden="true"><circle cx="5" cy="5" r="4.5"/></svg>
          www.norvale.com.au
        </p>
      </div>
    </div>
  </section>

  <section class="card card-back" aria-label="Business card back">
    <p class="specialism">Property Development<br>&amp; Site Acquisition Specialists</p>
    <div class="brand">
      <span class="brand-square"></span>
      <span class="brand-name">Norvale Property Group</span>
    </div>
    <p class="invite">Ask me about our <span class="highlight">Investment &amp; Partnership</span> opportunities</p>
  </section>

</body>
</html>
```